New Business Card Design Project

We require a business card design for Vexalund, a newly established Indian company.
Our focus is on the development, manufacturing, and export of a diverse array of pharmaceutical products on a global scale. The card should convey a professional appearance, as our primary markets are in Africa, China, and Southeast Asian nations.
We envision a two-sided business card, with the reverse side dedicated to a logo set against a solid color or an elegantly designed pattern. The corners should be rounded. We would appreciate seeing both horizontal and vertical design options. We trust the designer to utilize their expertise in creating this design.

The content for the business card is included in the attached Word file.

Target Market(s)

Our primary markets are in Africa, China, and Southeast Asian, Latin America, Maldives, Sri Lanka

Industry/Entity Type

Pharmaceutical Manufacturing and Export

Contact Information for Business Card

Colors

Designer to choose colors to be used in the design.

Requirements
Must have
• The reverse side of the business card features solely the logo along with the tagline, "Remedies of Life."
Should not have
• The logo should not exceed two instances, encompassing both the front and back sides of the card.

```html
<!DOCTYPE html>
<html lang="en">
<head>
<meta charset="UTF-8">
<title>Vexalund – Business Card</title>
<link rel="stylesheet" href="https://fonts.googleapis.com/css2?family=Poppins:wght@400;600&display=swap">
<style>
  :root {
    --backdrop: #2b2b2d;
    --card: #ffffff;
    --brand-blue: #29a8e0;
    --brand-red: #f0624d;
    --ink: #3a3a3a;
    --faint-blue: #e8f5fb;
  }
  * { margin: 0; padding: 0; box-sizing: border-box; }
  html, body { width: 1200px; height: 1200px; overflow: hidden; }
  body {
    background: var(--backdrop);
    font-family: "Poppins", sans-serif;
    display: flex;
    align-items: center;
    justify-content: center;
    gap: 60px;
  }
  .card {
    position: relative;
    width: 440px;
    height: 720px;
    background: var(--card);
    border-radius: 34px;
    overflow: hidden;
  }
  .card-front__decor {
    position: absolute;
    left: 110px;
    top: 60px;
    width: 230px;
    height: 230px;
    border-radius: 50%;
    background: var(--faint-blue);
  }
  .card-front__details {
    position: absolute;
    left: 52px;
    top: 330px;
    right: 40px;
    color: var(--ink);
  }
  .person-name {
    font-weight: 600;
    font-size: 29px;
    color: var(--brand-blue);
    line-height: 1.1;
  }
  .person-role {
    font-size: 17px;
    line-height: 1.35;
    margin-top: 4px;
  }
  .divider {
    width: 14px;
    height: 2px;
    background: var(--brand-blue);
    margin: 22px 0;
  }
  .address {
    font-size: 17px;
    line-height: 1.4;
  }
  .contact-list { list-style: none; }
  .contact-list li {
    display: flex;
    align-items: center;
    gap: 10px;
    font-size: 17px;
    line-height: 1.75;
  }
  .contact-icon { width: 14px; height: 14px; flex: none; }
  .card-back {
    display: flex;
    flex-direction: column;
    align-items: center;
    justify-content: center;
    gap: 10px;
  }
  .brand-row {
    display: flex;
    align-items: center;
    gap: 14px;
  }
  .brand-dot {
    width: 22px;
    height: 22px;
    border-radius: 50%;
    background: var(--brand-red);
  }
  .brand-name {
    font-weight: 600;
    font-size: 58px;
    line-height: 1.1;
    color: var(--brand-blue);
    letter-spacing: 0.5px;
  }
  .brand-tagline {
    font-size: 18px;
    color: var(--ink);
    letter-spacing: 2px;
  }
</style>
</head>
<body>
  <section class="card card-front">
    <div class="card-front__decor" role="img" aria-label="Faint brand decoration"></div>
    <div class="card-front__details">
      <h1 class="person-name">Arvind K. Solanke</h1>
      <p class="person-role">CEO<br>Vexalund</p>
      <div class="divider"></div>
      <p class="address">14, Nilgiri Colony, 440213<br>Wardha, India</p>
      <div class="divider"></div>
      <ul class="contact-list">
        <li>
          <svg class="contact-icon" viewBox="0 0 16 16"><path fill="#f0624d" d="M3 1h3l1 4-2 1c1 2 3 4 5 5l1-2 4 1v3c0 1-1 2-2 2C7 15 1 9 1 3c0-1 1-2 2-2z"/></svg>
          +919812573406
        </li>
        <li>
          <svg class="contact-icon" viewBox="0 0 16 16"><rect x="1" y="3" width="14" height="10" rx="1" fill="#f0624d"/><path d="M1.5 4l6.5 5 6.5-5" stroke="#fff" stroke-width="1.4" fill="none"/></svg>
          asolanke@vexalund.com
        </li>
        <li>
          <svg class="contact-icon" viewBox="0 0 16 16"><circle cx="8" cy="8" r="7" fill="#f0624d"/><path d="M1 8h14M8 1c-3 3-3 11 0 14M8 1c3 3 3 11 0 14" stroke="#fff" stroke-width="1.1" fill="none"/></svg>
          www.vexalund.com
        </li>
      </ul>
    </div>
  </section>

  <section class="card card-back">
    <div class="brand-row">
      <span class="brand-dot"></span>
      <span class="brand-name">Vexalund</span>
    </div>
    <p class="brand-tagline">Remedies of Life</p>
  </section>
</body>
</html>
```